Fitness Equipment & Service

I want to make the card eye catching and fun. We are called Corvane Motion Limited and we are based in Wales. We sell, install and service all types of fitness equipment from Skipping ropes, right through the Dumbbells, Kettle bells and Barbells through to state of the art Treadmills, Running Machines and Strength Equipment. We also design and install changing room furniture and lockers.

TYPOGRAPHY
We would like to use Futrura. Futura has an appearance of efficiency and forwardness. The typeface is derived
from simple geometric forms (near-perfect circles, triangles and squares) and is based on strokes of
near-even weight, which are low in contrast. This is most visible in the almost perfectly round stroke of
the o, which is nonetheless slightly ovoid.
The lowercase has tall ascenders, which rise above the cap line. The uppercase
characters present proportions similar to those of classical Roman capitals.

TYPOGRAPHIC CONSIDERATIONS
No Strike though
No Horizontal Scaling
No Drop Shadows
No Effects
Never use less than 120% Leading

OUR CORPORATE COLOURS
BRAND GUIDELINES
We were thinking that our primary colour palette consists of the Acid Green (Pantone 382) and Process Black.

We work closely with tquarly Ltd and would like to include their name on the card somewhere. I have attached images of the other brands that we work with as an idea or the small icons I have included that illustrate what we do?. I have very kindly been given permission to use any of the images off the files that I have included below, so I hope these help. I will include these below. I would be open to suggestions if it made the card more striking Can you do it?
Updates

Hi All, Just wanted to add a few thoughts but you are the guys with the creative visions (thats why are here) We are based in Wales, UK and we would be open to lots of different ideas on a theme but must be eye catching, Bold and FUN. If you can or think that the Welsh or any dragon could be put in there then go for it (its not a must have) We have also added some ideas for colour but again its over to you!! GO FOR IT ! Thanks and look forward to your visions! Owen

Hi All, Just thought I would sen through the contact details that need to be on the card. (if you want to play around with icons instead of the wording twitter, Facebook, go for it): Corvane Motion Limited Owen Pritchard Managing Director Mob: +44 (0)7582 913 406 e-mail: sales@corvanemotion.co.uk Web: Corvanemotion.co.uk twitter: @motionLetterbin Facebook: Corvane Motion Limited

```html
<!DOCTYPE html>
<html lang="en">
<head>
<meta charset="utf-8">
<title>Corvane Motion Limited – Business Card</title>
<link rel="stylesheet" href="https://fonts.googleapis.com/css2?family=Jost:wght@400;500;600;700&display=swap">
<style>
  :root {
    --bg: #e9e7e3;
    --blue-deep: #1d4f99;
    --blue-mid: #2a6ebd;
    --blue-light: #4f97d8;
    --blue-pale: #a9c3dc;
    --navy: #17306b;
    --white: #ffffff;
    --ink: #111111;
    --band: #0b0b0b;
  }
  * { box-sizing: border-box; margin: 0; padding: 0; }
  html, body {
    width: 1200px; height: 892px; overflow: hidden;
    background: var(--bg);
    font-family: "Jost", "Futura", sans-serif;
  }
  .canvas {
    position: relative; width: 1200px; height: 892px;
    display: flex; align-items: center; justify-content: center; gap: 40px;
  }
  .card {
    position: relative; width: 540px; height: 310px;
    background: var(--white); overflow: hidden;
    box-shadow: 0 10px 30px rgba(0,0,0,0.18);
  }

  /* Front */
  .card-front__shape { position: absolute; inset: 0; }
  .brand-mark {
    position: absolute; left: 36px; top: 34px;
    display: flex; align-items: center; gap: 14px;
    color: var(--white); font-weight: 600; font-size: 22px; line-height: 1.2;
  }
  .brand-mark__dot {
    width: 58px; height: 58px; border-radius: 50%;
    background: var(--navy); border: 4px solid var(--white); flex: none;
  }
  .contact {
    position: absolute; right: 30px; top: 96px;
    text-align: right; color: var(--ink); line-height: 1.25;
  }
  .contact__name { font-size: 25px; font-weight: 700; }
  .contact__role { font-size: 13px; font-weight: 500; margin-bottom: 14px; }
  .contact__line {
    display: flex; justify-content: flex-end; align-items: center; gap: 7px;
    font-size: 15px; font-weight: 600;
  }
  .contact__icon {
    width: 13px; height: 13px; background: var(--blue-mid); flex: none;
    display: flex; align-items: center; justify-content: center;
  }
  .social-band {
    position: absolute; left: 18px; bottom: 16px; width: 380px; height: 24px;
    background: var(--band); color: var(--white);
    display: flex; align-items: center; gap: 8px; padding: 0 8px;
    font-size: 13px; font-weight: 600; line-height: 1.2; white-space: nowrap;
  }
  .social-band__mark { width: 14px; height: 14px; background: var(--blue-light); flex: none; }
  .social-band__gap { width: 14px; }

  /* Back */
  .card-back { padding: 10px; }
  .card-back__field {
    position: relative; width: 100%; height: 100%;
    background: var(--blue-mid); overflow: hidden;
  }
  .tiles { position: absolute; inset: 0; }
  .action-photo {
    position: absolute; left: 250px; top: 60px; width: 200px; height: 170px;
    border-radius: 50%;
    background: radial-gradient(circle at 40% 40%, #3a5f97, #1a2e55 75%);
    opacity: 0.55;
  }
  .back-mark {
    position: absolute; left: 22px; top: 22px; width: 200px; height: 200px;
    border-radius: 50%; background: var(--white);
    display: flex; align-items: center; justify-content: center; text-align: center;
    color: var(--navy); font-weight: 600; font-size: 22px; line-height: 1.2; padding: 24px;
  }
</style>
</head>
<body>
<main class="canvas">

  <section class="card card-front" aria-label="Business card front">
    <svg class="card-front__shape" width="540" height="310" viewBox="0 0 540 310" aria-hidden="true">
      <defs>
        <linearGradient id="frontBlue" x1="0" y1="0" x2="1" y2="1">
          <stop offset="0" stop-color="#4f97d8"/>
          <stop offset="0.55" stop-color="#2a6ebd"/>
          <stop offset="1" stop-color="#1d4f99"/>
        </linearGradient>
      </defs>
      <polygon points="0,0 540,0 540,18 0,255" fill="url(#frontBlue)"/>
    </svg>

    <div class="brand-mark">
      <span class="brand-mark__dot"></span>
      <span>Corvane Motion<br>Limited</span>
    </div>

    <div class="contact">
      <div class="contact__name">Owen Pritchard</div>
      <div class="contact__role">Managing Director</div>
      <div class="contact__line">+44 (0)7582 913 406
        <span class="contact__icon"><svg width="9" height="9" viewBox="0 0 10 10"><path d="M2 1h2l1 2-1 1a6 6 0 0 0 2 2l1-1 2 1v2a1 1 0 0 1-1 1A8 8 0 0 1 1 2a1 1 0 0 1 1-1z" fill="#fff"/></svg></span>
      </div>
      <div class="contact__line">sales@corvanemotion.co.uk
        <span class="contact__icon"><svg width="9" height="9" viewBox="0 0 10 10"><rect x="1" y="2.5" width="8" height="5" fill="none" stroke="#fff"/><path d="M1 2.5l4 3 4-3" fill="none" stroke="#fff"/></svg></span>
      </div>
      <div class="contact__line">Corvanemotion.co.uk
        <span class="contact__icon"><svg width="9" height="9" viewBox="0 0 10 10"><circle cx="5" cy="5" r="3.8" fill="none" stroke="#fff"/><path d="M1.2 5h7.6M5 1.2v7.6" stroke="#fff"/></svg></span>
      </div>
    </div>

    <div class="social-band">
      <span class="social-band__mark"></span>
      <span>Corvane Motion Limited</span>
      <span class="social-band__gap"></span>
      <span class="social-band__mark"></span>
      <span>@motionLetterbin</span>
    </div>
  </section>

  <section class="card card-back" aria-label="Business card back">
    <div class="card-back__field">
      <svg class="tiles" width="520" height="290" viewBox="0 0 520 290" aria-hidden="true">
        <rect x="0" y="0" width="520" height="290" fill="#2a6ebd"/>
        <rect x="180" y="0" width="70" height="60" fill="#4f97d8"/>
        <rect x="250" y="0" width="70" height="60" fill="#1d4f99"/>
        <rect x="390" y="0" width="70" height="60" fill="#4f97d8"/>
        <rect x="250" y="60" width="70" height="60" fill="#1d4f99"/>
        <rect x="320" y="60" width="70" height="60" fill="#4f97d8"/>
        <rect x="460" y="60" width="60" height="60" fill="#1d4f99"/>
        <rect x="180" y="120" width="70" height="60" fill="#1d4f99"/>
        <rect x="390" y="120" width="70" height="60" fill="#1d4f99"/>
        <rect x="180" y="180" width="70" height="60" fill="#a9c3dc"/>
        <rect x="320" y="180" width="70" height="60" fill="#1d4f99"/>
        <rect x="390" y="180" width="70" height="60" fill="#4f97d8"/>
        <rect x="0" y="240" width="110" height="50" fill="#1d4f99"/>
        <rect x="250" y="240" width="70" height="50" fill="#a9c3dc"/>
        <rect x="460" y="240" width="60" height="50" fill="#1d4f99"/>
      </svg>
      <div class="action-photo" role="img" aria-label="Faint photograph of a kettlebell behind the tiles"></div>
      <div class="back-mark">Corvane Motion Limited</div>
    </div>
  </section>

</main>
</body>
</html>
```